We need a business card for our gym. We are a PowerCore affiliate in Decatur Georgie established 2008. Our company name is Rally Functional Fitness. PowerCore Building Prime Fitness. Instagram and website is @rallygym. Hashtags we use #rallywithheart #madetorally We want something similar to the the black and neon green design attached but a different color scheme. No neon colors. Are company colors are the same as the blue and white card attached. We are open to ideas as far as colors however - just no neon.

Contact Information for Business Card

Rally Functional Fitness
472 Halvern Drive
Decatur GA 30041
Phone 404.555.0187 Website www.rallygym.example

Font styles to use
Other font styles liked:
• Futura Extra Bold Condensed

Colors

Designer to choose colors to be used in the design.

Requirements
Must have
• Our primary font we typically use for our name is Futura Extra Bold Condensed
Nice to have
• I attached a card from that is black and neon green from Zorva that we would like something similar. The blue and white is more similar to our colors. We also use have used black and white in the past. We use the chevrons as out logo. We are a PowerCore affiliate so I included a logo from them as well that may or may not be used on the card. Our instagram is @rallygym hashtags #madetorally #rallywithheart
Should not have
• No neon colors

```html
<!DOCTYPE html>
<html lang="en">
<head>
<meta charset="utf-8">
<title>Rally Functional Fitness – Business Card</title>
<link href="https://fonts.googleapis.com/css2?family=Anton&family=Montserrat:wght@400;500&display=swap" rel="stylesheet">
<style>
  :root {
    --backdrop: #d3d3d3;
    --brand-blue: #14599a;
    --brand-blue-light: #1a80c4;
    --ink-blue: #1769ad;
    --card-white: #ffffff;
    --rule: #3f6fb3;
  }
  * { margin: 0; padding: 0; box-sizing: border-box; }
  html, body { width: 1200px; height: 800px; overflow: hidden; }
  body {
    background: var(--backdrop);
    position: relative;
    font-family: "Montserrat", sans-serif;
  }
  .card {
    position: absolute;
    top: 251px;
    width: 520px;
    height: 297px;
    box-shadow: 0 2px 6px rgba(0,0,0,0.18);
  }
  .card--front {
    left: 50px;
    background: linear-gradient(100deg, var(--brand-blue) 0%, var(--brand-blue-light) 32%, var(--brand-blue) 62%, var(--brand-blue) 100%);
    display: flex;
    align-items: center;
    justify-content: center;
  }
  .front-name {
    font-family: "Anton", sans-serif;
    font-weight: 400;
    font-size: 96px;
    letter-spacing: 2px;
    color: var(--card-white);
    text-transform: uppercase;
  }
  .card--back {
    left: 630px;
    background: var(--card-white);
  }
  .back-name {
    position: absolute;
    left: 34px;
    top: 96px;
    width: 190px;
    font-family: "Anton", sans-serif;
    font-weight: 400;
    font-size: 27px;
    line-height: 1.05;
    color: var(--ink-blue);
    text-transform: uppercase;
  }
  .back-name .big { display: block; font-size: 74px; line-height: 1; }
  .divider {
    position: absolute;
    left: 258px;
    top: 78px;
    width: 1px;
    height: 140px;
    background: var(--rule);
  }
  .contact {
    position: absolute;
    left: 282px;
    top: 78px;
    color: var(--ink-blue);
    font-size: 12.5px;
    line-height: 1.3;
  }
  .contact__name {
    font-family: "Anton", sans-serif;
    font-size: 18px;
    letter-spacing: 1.5px;
    text-transform: uppercase;
  }
  .contact__role { text-transform: uppercase; margin-bottom: 10px; }
  .contact__address { margin-bottom: 10px; }
  .contact__line { display: flex; align-items: center; gap: 6px; }
  .contact__line svg { width: 11px; height: 11px; flex: none; }
</style>
</head>
<body>
  <section class="card card--front" aria-label="Card front">
    <span class="front-name">Rally</span>
  </section>

  <section class="card card--back" aria-label="Card back">
    <p class="back-name"><span class="big">Rally</span>Functional Fitness</p>
    <div class="divider"></div>
    <div class="contact">
      <p class="contact__name">Marcus &nbsp;Delling</p>
      <p class="contact__role">Expert Coaches</p>
      <p class="contact__address">472 Halvern Drive<br>Decatur GA 30041</p>
      <p class="contact__line">
        <svg viewBox="0 0 24 24" aria-hidden="true"><path fill="currentColor" d="M6.6 10.8a15.1 15.1 0 0 0 6.6 6.6l2.2-2.2a1 1 0 0 1 1-.25 11.4 11.4 0 0 0 3.6.57 1 1 0 0 1 1 1V20a1 1 0 0 1-1 1A17 17 0 0 1 3 4a1 1 0 0 1 1-1h3.5a1 1 0 0 1 1 1c0 1.25.2 2.45.57 3.57a1 1 0 0 1-.25 1z"/></svg>
        404.555.0187
      </p>
      <p class="contact__line">
        <svg viewBox="0 0 24 24" aria-hidden="true"><circle cx="12" cy="12" r="10" fill="none" stroke="currentColor" stroke-width="2"/><path d="M2 12h20M12 2c3 3 3 17 0 20M12 2c-3 3-3 17 0 20" fill="none" stroke="currentColor" stroke-width="1.6"/></svg>
        www.rallygym.example
      </p>
    </div>
  </section>
</body>
</html>
```